Social Media Graphics - Oakline Push REVISED

Create 6-7 individual social media graphics (square size) to encourage folks to join our online course called:

The Harvest Ledger Circle
How to Launch a Multi-Million Business From Scratch
Sign Up Today!

IMPORTANT: Make the largest and most prominent text on the graphic be: How to Launch a Multi-Million Business From Scratch

For the color scheme of the graphics, let's try a blue color palette; make sure the graphics appeal to both men and women

Make sure each graphic contains 1 of the 3 pics attached (crop pic as needed); and make sure one of the graphics is all TEXT only.

Target Market(s)

men and women looking to start a business

Industry/Entity Type

Entrepreneurship

Colors
0054AA
0677BA
7BADD7
CADEEF
E8F1F8

Requirements
Must have
• All the text and use the 3 pics provided; one graphic can be all text; Simple, modern design that's easy to read

```html
<!DOCTYPE html>
<html lang="en">
<head>
<meta charset="utf-8">
<title>The Harvest Ledger Circle – How to Launch a Multi-Million Business From Scratch</title>
<link rel="stylesheet" href="https://fonts.googleapis.com/css2?family=Anton&family=Oswald:wght@700&display=swap">
<style>
  :root {
    --navy-deep: #003c6c;
    --navy: #00467e;
    --sky: #0a8fd6;
    --sky-bright: #1ba3ef;
    --panel: #2c191b;
    --white: #ffffff;
    --photo-a: #1c2d44;
    --photo-b: #c9364f;
  }
  html, body {
    margin: 0;
    padding: 0;
    width: 1200px;
    height: 1200px;
    overflow: hidden;
  }
  .social-graphic {
    position: relative;
    width: 1200px;
    height: 1200px;
    overflow: hidden;
    background:
      radial-gradient(ellipse 700px 620px at 1150px 60px, #0096de 0%, rgba(0,150,222,0) 100%),
      radial-gradient(ellipse 500px 400px at 1150px 620px, #0a7fc0 0%, rgba(10,127,192,0) 100%),
      linear-gradient(90deg, var(--navy-deep) 0%, var(--navy) 45%, #0068a8 100%);
    font-family: "Anton", "Oswald", sans-serif;
    color: var(--white);
  }
  .course-name {
    position: absolute;
    left: 132px;
    top: 168px;
    margin: 0;
    font-weight: 400;
    line-height: 1;
    text-transform: uppercase;
  }
  .course-name span { display: block; white-space: nowrap; }
  .course-name .word-the { font-size: 112px; letter-spacing: 2px; }
  .course-name .word-harvest { font-size: 104px; letter-spacing: 1px; margin-top: 18px; }
  .course-name .word-ledger { font-size: 58px; letter-spacing: 1px; margin-top: 24px; }

  .hosts-photo {
    position: absolute;
    left: 531px;
    top: 68px;
    width: 546px;
    height: 516px;
    border-radius: 220px 220px 0 0;
    background: linear-gradient(90deg, var(--photo-b) 0%, var(--photo-b) 48%, var(--photo-a) 52%, var(--photo-a) 100%);
    opacity: 0.9;
  }

  .headline-panel {
    position: absolute;
    left: 70px;
    top: 584px;
    width: 1048px;
    height: 490px;
    border-radius: 26px;
    background: var(--panel);
  }
  .headline {
    margin: 0;
    position: absolute;
    inset: 0;
    font-weight: 400;
    text-transform: uppercase;
    text-align: center;
    line-height: 1;
  }
  .headline span { position: absolute; left: 0; right: 0; white-space: nowrap; }
  .headline .line-1 { top: 36px; font-size: 152px; letter-spacing: 7px; }
  .headline .line-2 { top: 228px; font-size: 152px; letter-spacing: 4px; }
  .headline .line-3 { top: 380px; font-size: 82px; letter-spacing: 3px; }

  .call-to-action {
    position: absolute;
    left: 57px;
    right: 69px;
    top: 1118px;
    height: 44px;
    display: flex;
    align-items: center;
    gap: 28px;
  }
  .call-to-action .rule {
    flex: 1;
    height: 4px;
    background: var(--sky-bright);
  }
  .call-to-action .label {
    font-family: "Oswald", sans-serif;
    font-weight: 700;
    font-size: 38px;
    letter-spacing: 8px;
    color: var(--sky-bright);
    text-transform: uppercase;
    line-height: 1;
  }
</style>
</head>
<body>
  <main class="social-graphic">
    <h2 class="course-name">
      <span class="word-the">The</span>
      <span class="word-harvest">Harvest</span>
      <span class="word-ledger">Ledger Circle</span>
    </h2>

    <div class="hosts-photo" role="img" aria-label="Photo of the two course hosts, a smiling woman in a pink dress with arms crossed and a smiling man in a black t-shirt and jacket"></div>

    <section class="headline-panel">
      <h1 class="headline">
        <span class="line-1">How to Launch</span>
        <span class="line-2">A Multi-Million</span>
        <span class="line-3">Business From Scratch</span>
      </h1>
    </section>

    <div class="call-to-action">
      <span class="rule"></span>
      <span class="label">Sign Up Today</span>
      <span class="rule"></span>
    </div>
  </main>
</body>
</html>
```